Business Card Design For A Cajun Seafood Restaurant

We are opening a cajun seafood restaurant in a week. We mainly serve cajun seafood which is orginally from Louisiana. We want design on both sides of a business card. I have menu on the website. You can go to www.reednkettle.example to check out our menu.

Restaurant name: Reed N' Kettle
Phone: +1 (555) 304-7712
Address: 48206 Ludlow Row, #7, Bexmoor Flats, Ca90000
Email: reednkettle@mailbox.example
Website: www.reednkettle.example

Maybe add social media icons (facebook, instagram) if looks nice on the business card.
facebook.com/reednkettle
instagram.com/reednkettle or @reednkettle

Attached is the logo and other business card samples that I like.

```html
<!DOCTYPE html>
<html lang="en">
<head>
<meta charset="utf-8">
<title>Reed N' Kettle – Business Card</title>
<link href="https://fonts.googleapis.com/css2?family=PT+Sans:wght@400;700&display=swap" rel="stylesheet">
<style>
  :root {
    --backdrop: #3a3533;
    --card-white: #f7f7f5;
    --card-black: #141414;
    --ink: #2b2b2b;
    --orange: #f26a1b;
    --gold: #f2c230;
    --rule: #5a5a5a;
    --art-light: #f7a23a;
    --art-dark: #d9561a;
  }
  * { box-sizing: border-box; margin: 0; padding: 0; }
  html, body { width: 1200px; height: 900px; overflow: hidden; }
  body {
    background: var(--backdrop);
    font-family: "PT Sans", Arial, sans-serif;
    position: relative;
  }
  .card {
    position: absolute;
    left: 250px;
    width: 700px;
    height: 400px;
    border-radius: 4px;
    overflow: hidden;
  }
  .card--front { top: 475px; background: var(--card-white); color: var(--ink); }
  .card--back  { top: 35px;  background: var(--card-black); }

  .brand { position: absolute; text-align: center; }
  .brand__art {
    display: block;
    margin: 0 auto;
    width: 130px;
    height: 110px;
    border-radius: 50% 50% 40% 40%;
    background: radial-gradient(circle at 50% 40%, var(--art-light), var(--art-dark));
  }
  .brand__name {
    display: block;
    margin-top: 10px;
    font-weight: 700;
    font-size: 34px;
    letter-spacing: 1px;
    text-transform: uppercase;
    white-space: nowrap;
  }
  .card--front .brand { left: 300px; top: 36px; width: 300px; }
  .card--front .brand__name { color: var(--ink); }
  .card--back .brand { left: 200px; top: 60px; width: 300px; }
  .card--back .brand__name { color: var(--gold); }

  .social-tab {
    position: absolute;
    left: 0; top: 190px;
    width: 120px; height: 62px;
    background: var(--orange);
    clip-path: polygon(0 0, 112px 0, 112px 10px, 120px 18px, 120px 44px, 112px 52px, 112px 62px, 0 62px);
    display: flex; align-items: center; justify-content: center; gap: 14px;
    padding-right: 8px;
  }
  .social-tab__icon {
    width: 26px; height: 26px;
    border-radius: 6px;
    border: 3px solid var(--card-white);
  }

  .contact { position: absolute; font-size: 19px; line-height: 1; white-space: nowrap; }
  .contact__label { color: var(--orange); font-weight: 700; margin-right: 6px; }
  .contact--email { left: 330px; top: 222px; }
  .contact--phone { left: 100px; top: 276px; }
  .contact--web { left: 100px; top: 304px; color: var(--orange); font-weight: 700; }
  .contact--address { left: 100px; top: 344px; }

  .rule { position: absolute; height: 1px; background: var(--rule); }
  .rule--upper { left: 520px; top: 236px; width: 180px; }
  .rule--lower { left: 330px; top: 330px; width: 370px; }
  .back-web {
    position: absolute; left: 0; top: 288px; width: 700px;
    text-align: center; color: var(--orange); font-weight: 700; font-size: 18px;
  }
</style>
</head>
<body>
  <section class="card card--back" aria-label="Business card, back">
    <div class="brand">
      <span class="brand__art" role="img" aria-label="Illustrated crab mascot holding corn"></span>
      <span class="brand__name">Reed N' Kettle</span>
    </div>
    <div class="rule rule--upper"></div>
    <div class="back-web">www.reednkettle.example</div>
    <div class="rule rule--lower"></div>
  </section>

  <section class="card card--front" aria-label="Business card, front">
    <div class="brand">
      <span class="brand__art" role="img" aria-label="Illustrated crab mascot holding corn"></span>
      <span class="brand__name">Reed N' Kettle</span>
    </div>
    <div class="social-tab" aria-label="Social media">
      <span class="social-tab__icon"></span>
      <span class="social-tab__icon"></span>
    </div>
    <p class="contact contact--email"><span class="contact__label">E:</span>reednkettle@mailbox.example</p>
    <p class="contact contact--phone"><span class="contact__label">M:</span>+1 (555) 304-7712</p>
    <p class="contact contact--web">www.reednkettle.example</p>
    <p class="contact contact--address">48206 Ludlow Row, #7, Bexmoor Flats, Ca90000</p>
  </section>
</body>
</html>
```